BOLD & MINIMALIST DESIGN NEEDED

We want a very bold but minimalistic business card design that is impactful and utilizes both sides of the business card. Our current logo is included for your use.

We want bold fonts and good use of negative space. We don't want the logo to overpower the design.

Target Market(s)

Professionals who are building new commercial buildings.

Industry/Entity Type

Construction

Contact Information for Business Card

Name, Title, email, office phone, cell phone, website

Font styles to use
Serif
Sans Serif

Requirements
Must have
• Bold design!

```html
<!DOCTYPE html>
<html lang="en">
<head>
<meta charset="utf-8">
<title>Ridgeway Design + Build — Business Card</title>
<link href="https://fonts.googleapis.com/css2?family=Montserrat:wght@500;600;800&display=swap" rel="stylesheet">
<style>
  :root {
    --backdrop: #939393;
    --ink: #0b0c0e;
    --paper: #ffffff;
    --green: #8fd14f;
    --divider: #4a4a4a;
  }
  * { margin: 0; padding: 0; box-sizing: border-box; }
  html, body { width: 1200px; height: 1200px; overflow: hidden; }
  body {
    background: var(--backdrop);
    font-family: "Montserrat", sans-serif;
    position: relative;
  }
  .card {
    position: absolute;
    left: 179px;
    width: 861px;
    height: 496px;
    overflow: hidden;
  }
  .card--front { top: 84px; background: var(--ink); }
  .card--back { top: 621px; background: var(--paper); }

  .brand {
    position: absolute;
    left: 0; right: 0;
    display: flex;
    align-items: center;
    justify-content: center;
    gap: 16px;
    font-weight: 800;
    font-size: 38px;
    letter-spacing: 1px;
    text-transform: uppercase;
  }
  .brand__square { width: 22px; height: 22px; background: var(--green); flex: none; }
  .card--front .brand { top: 225px; color: var(--paper); }
  .card--back .brand { top: 70px; color: var(--ink); }

  .back__ground { position: absolute; left: 0; top: 270px; width: 861px; height: 226px; }

  .holder {
    position: absolute;
    right: 405px;
    top: 358px;
    text-align: right;
  }
  .holder__name { color: var(--paper); font-weight: 600; font-size: 33px; line-height: 1; }
  .holder__title { color: var(--green); font-weight: 500; font-size: 28px; line-height: 1; margin-top: 10px; }

  .contact-divider {
    position: absolute;
    left: 481px; top: 338px;
    width: 1px; height: 132px;
    background: var(--divider);
  }
  .contacts {
    position: absolute;
    left: 492px; top: 332px;
    list-style: none;
  }
  .contacts li {
    display: flex;
    align-items: center;
    height: 34px;
    color: var(--paper);
    font-weight: 500;
    font-size: 22px;
    letter-spacing: 0.5px;
  }
  .contacts svg { width: 22px; height: 22px; margin-right: 18px; flex: none; }
  .accent { color: var(--green); }
</style>
</head>
<body>

<section class="card card--front">
  <div class="brand"><span class="brand__square"></span>Ridgeway Design + Build</div>
</section>

<section class="card card--back">
  <div class="brand"><span class="brand__square"></span>Ridgeway Design + Build</div>

  <svg class="back__ground" viewBox="0 0 861 226" aria-hidden="true">
    <path d="M0 27 H343 Q430 5 517 27 H861 V226 H0 Z" fill="var(--ink)"/>
    <path d="M0 25 H343 Q430 3 517 25 H861" fill="none" stroke="var(--green)" stroke-width="3"/>
  </svg>

  <div class="holder">
    <p class="holder__name">Name Surename</p>
    <p class="holder__title">Director</p>
  </div>

  <div class="contact-divider"></div>

  <ul class="contacts">
    <li>
      <svg viewBox="0 0 24 24" fill="var(--green)" aria-hidden="true"><path d="M6.6 10.8a15 15 0 0 0 6.6 6.6l2.2-2.2a1 1 0 0 1 1-.25 11.4 11.4 0 0 0 3.6.57 1 1 0 0 1 1 1V20a1 1 0 0 1-1 1A17 17 0 0 1 3 4a1 1 0 0 1 1-1h3.5a1 1 0 0 1 1 1c0 1.25.2 2.45.57 3.57a1 1 0 0 1-.25 1z"/></svg>
      555-014-2200
    </li>
    <li>
      <svg viewBox="0 0 24 24" fill="var(--green)" aria-hidden="true"><path d="M2 8c2-3 18-3 20 0v2h-5V8.5c-2-.7-8-.7-10 0V10H2z"/><path d="M7 11h10l3 9H4z"/></svg>
      555-014-2200
    </li>
    <li>
      <svg viewBox="0 0 24 24" fill="var(--green)" aria-hidden="true"><path d="M2 5h20v14H2z"/><path d="M2 5l10 8 10-8M2 19l7-7M22 19l-7-7" stroke="var(--ink)" stroke-width="1.6" fill="none"/></svg>
      info@ridgeway-db.com
    </li>
    <li>
      <svg viewBox="0 0 24 24" fill="none" stroke="var(--green)" stroke-width="1.8" aria-hidden="true"><circle cx="12" cy="12" r="10"/><ellipse cx="12" cy="12" rx="4.5" ry="10"/><path d="M2 12h20M4 7h16M4 17h16"/></svg>
      www.<span class="accent">ridgeway-db</span>.com
    </li>
  </ul>
</section>

</body>
</html>
```